Recto Verso Audiology Business Card

Business card with a beautiful design on the back. On the Recto you need the following data Lindqvist Oren Audiologist Hearing Solutions Hearing Protection Tinnitus Hyperacusis Tel: 0482/37 59 08 Email: On the back, you need something nice like the attached file. The logo "Corra Luna" can be in the center The colors of the Logo can not be changed If possible stay in the same colors as the logo Another solution is to put the logo on the front and have a nice back (A mosaic of small ears, hearing aids or other ..) Thank you _______________________________________________________________ Visit card On the Recto Lindqvist Oren Audiologist Hearing Solutions Hearing Protection Tinnitus Hyperacusis Tel: 0482/37 59 08 Email: You can put the logo " Corra Luna "on the Recto of the Verso The colors of the logo can not be changed. If you put the logo on the back, it must be well integrated. On the Verso I need something in the files. something stylish. It's a visit card for an audiologist. You can get ears of hearing aids if you need. Thanks

Target Market(s)

customers

Contact Information for Business Card

Carte de visite standard ou A6

Font styles to use
Serif
Sans Serif

Colors
33a6d7

Requirements
Must have
• the logo and a stylized background.
Nice to have
• It would be nice to have a back side related to audiology (ears, hearing aids etc.)

```html
<!DOCTYPE html>
<html lang="en">
<head>
<meta charset="utf-8">
<title>Corra Luna Audiology Business Card – Recto and Verso</title>
<link href="https://fonts.googleapis.com/css2?family=Ubuntu:wght@400;500&display=swap" rel="stylesheet">
<style>
  :root {
    --backdrop: #2b2623;
    --card-black: #16191c;
    --card-black-deep: #101214;
    --accent-cyan: #5fc7d6;
    --muted-grey: #56606a;
    --contact-grey: #c9ced2;
    --foil-gold: #c9a24a;
    --gold-shadow: #4a3d1f;
    --gold-mid: #6e5a2c;
  }
  * { box-sizing: border-box; margin: 0; padding: 0; }
  html, body {
    width: 1200px;
    height: 769px;
    overflow: hidden;
    background: var(--backdrop);
    font-family: "Ubuntu", sans-serif;
  }
  .canvas {
    position: relative;
    width: 1200px;
    height: 769px;
  }
  .card {
    position: absolute;
    top: 234px;
    width: 520px;
    height: 300px;
    border-radius: 4px;
    overflow: hidden;
    box-shadow: 0 14px 30px rgba(0, 0, 0, 0.45);
  }

  /* Recto */
  .card-front {
    left: 50px;
    background: var(--card-black);
  }
  .front-logo {
    position: absolute;
    left: 38px;
    top: 120px;
    display: flex;
    align-items: center;
    gap: 10px;
    color: var(--accent-cyan);
    font-weight: 400;
    font-size: 19px;
    line-height: 1.1;
    text-transform: uppercase;
    letter-spacing: 0.5px;
  }
  .logo-square {
    width: 12px;
    height: 12px;
    background: currentColor;
    flex: none;
  }
  .contact-block {
    position: absolute;
    left: 262px;
    top: 70px;
  }
  .holder-name {
    color: var(--accent-cyan);
    font-weight: 500;
    font-size: 19px;
    letter-spacing: 0.4px;
    text-transform: uppercase;
  }
  .holder-role {
    color: var(--muted-grey);
    font-size: 13px;
    margin-top: 2px;
  }
  .contact-list {
    list-style: none;
    margin-top: 14px;
    color: var(--contact-grey);
    font-size: 12.5px;
    line-height: 1.45;
  }
  .services-band {
    position: absolute;
    left: 0;
    right: 0;
    top: 222px;
    height: 22px;
    background: var(--accent-cyan);
    color: #1e4b55;
    font-size: 12.5px;
    line-height: 22px;
    padding-left: 130px;
    white-space: nowrap;
  }
  .services-band .dot { margin: 0 5px; }

  /* Verso */
  .card-back {
    left: 630px;
    background: var(--card-black-deep);
  }
  .ear-field {
    position: absolute;
    inset: 0;
    background:
      radial-gradient(ellipse 60% 70% at 20% 20%, rgba(201, 162, 74, 0.22), transparent 70%),
      radial-gradient(ellipse 55% 65% at 85% 85%, rgba(201, 162, 74, 0.18), transparent 70%),
      radial-gradient(ellipse 50% 50% at 50% 50%, rgba(110, 90, 44, 0.35), transparent 80%),
      linear-gradient(135deg, #1d1a14 0%, var(--gold-shadow) 45%, #1a1812 100%);
  }
  .back-logo {
    position: absolute;
    left: 50%;
    top: 50%;
    transform: translate(-50%, -50%);
    display: flex;
    align-items: center;
    gap: 10px;
    color: var(--foil-gold);
    font-weight: 400;
    font-size: 22px;
    line-height: 1.1;
    text-transform: uppercase;
    letter-spacing: 0.5px;
    padding: 18px 22px;
    background: var(--card-black-deep);
  }
  .back-logo .logo-square {
    width: 13px;
    height: 13px;
  }
</style>
</head>
<body>
<main class="canvas">

  <section class="card card-front" aria-label="Business card front">
    <div class="front-logo">
      <span class="logo-square"></span>
      <span class="logo-name">Medical Center<br>Corra Luna</span>
    </div>

    <div class="contact-block">
      <h1 class="holder-name">Lindqvist Oren</h1>
      <p class="holder-role">Audiologist Hearing</p>
      <ul class="contact-list">
        <li>0482/37 59 08</li>
        <li>info@corralunahearing.com</li>
        <li>corralunahearing.com</li>
      </ul>
    </div>

    <div class="services-band">
      Solutions Hearing <span class="dot">•</span> Protection <span class="dot">•</span> Tinnitus <span class="dot">•</span> Hyperacusis
    </div>
  </section>

  <section class="card card-back" aria-label="Business card back">
    <div class="ear-field" role="img" aria-label="Stylized audiology background: repeating gold ears with sound waves on black"></div>
    <div class="back-logo">
      <span class="logo-square"></span>
      <span class="logo-name">Medical Center<br>Corra Luna</span>
    </div>
  </section>

</main>
</body>
</html>
```